need eczema bath soak label/bag

need you to recreate this please. ai file. recreate this exact image please. ...if you want a big tip, create some different styles.

Colors
0054AA
0677BA
7BADD7
CADEEF
E8F1F8

```html
<!DOCTYPE html>
<html lang="en">
<head>
<meta charset="UTF-8">
<title>The Shore Calmed Soak – Bath Soak Pouch</title>
<link href="https://fonts.googleapis.com/css2?family=Outfit:wght@400;500;800&display=swap" rel="stylesheet">
<style>
  :root {
    --backdrop: #032d2d;
    --ink: #234545;
    --pouch-white: #f2f3f3;
    --mist: #e6f1f0;
    --sea-deep: #3db5b2;
    --sea-light: #86d4cc;
    --foam: #f1f3f2;
    --wet-sand: #d6d1c4;
    --sand: #ddd0b0;
    --sand-light: #e7ddc4;
    --seal-line: #dadcdd;
  }
  * { margin: 0; padding: 0; box-sizing: border-box; }
  html, body {
    width: 1200px; height: 800px; overflow: hidden;
    background: var(--backdrop);
    font-family: "Outfit", sans-serif;
  }
  .canvas { position: relative; width: 1200px; height: 800px; }
  .pouch-shape { position: absolute; left: 0; top: 0; }
  .label {
    position: absolute; left: 396px; width: 400px;
    text-align: center; color: var(--ink); line-height: 1;
  }
  .title-lead { top: 220px; font-size: 25px; font-weight: 800; }
  .title-line { font-size: 54px; font-weight: 800; letter-spacing: -0.5px; }
  .title-first { top: 251px; }
  .title-second { top: 310px; }
  .title-third { top: 368px; }
  .claim { top: 432px; font-size: 13.5px; font-weight: 400; line-height: 16.5px; }
  .treatment { top: 493px; font-size: 14px; font-weight: 800; letter-spacing: 0.2px; }
  .net-weight { top: 516px; font-size: 17px; font-weight: 800; }
  .product-type { top: 546px; font-size: 11.5px; font-weight: 400; letter-spacing: 0.2px; }
  .brand {
    top: 670px; display: flex; align-items: center; justify-content: center; gap: 7px;
    font-size: 13px; font-weight: 800; letter-spacing: 2.4px;
  }
  .brand-dot { width: 9px; height: 9px; border-radius: 50%; background: var(--ink); }
</style>
</head>
<body>
  <main class="canvas">
    <svg class="pouch-shape" width="1200" height="800" viewBox="0 0 1200 800" role="img" aria-label="Stand-up pouch printed with an aerial photograph of turquoise waves washing onto a sandy beach">
      <defs>
        <linearGradient id="shore" gradientUnits="userSpaceOnUse" x1="0" y1="82" x2="0" y2="717">
          <stop offset="0" stop-color="var(--pouch-white)"/>
          <stop offset="0.33" stop-color="var(--pouch-white)"/>
          <stop offset="0.37" stop-color="var(--mist)"/>
          <stop offset="0.42" stop-color="var(--sea-light)"/>
          <stop offset="0.48" stop-color="var(--sea-deep)"/>
          <stop offset="0.54" stop-color="var(--sea-light)"/>
          <stop offset="0.59" stop-color="var(--foam)"/>
          <stop offset="0.64" stop-color="var(--foam)"/>
          <stop offset="0.72" stop-color="var(--wet-sand)"/>
          <stop offset="0.80" stop-color="var(--foam)"/>
          <stop offset="0.86" stop-color="var(--sand)"/>
          <stop offset="1" stop-color="var(--sand-light)"/>
        </linearGradient>
      </defs>
      <path fill="url(#shore)" d="M405 82 H788 Q802 82 802 96 V121 Q798 124 802 127 L773 690 Q773 717 748 717 H445 Q420 717 420 690 L391 127 Q395 124 391 121 V96 Q391 82 405 82 Z"/>
      <rect x="409" y="164" width="374" height="2" fill="var(--seal-line)"/>
      <rect x="409" y="172" width="374" height="2" fill="var(--seal-line)"/>
    </svg>

    <p class="label title-lead">THE</p>
    <h1 class="label title-line title-first">SHORE</h1>
    <p class="label title-line title-second">CALMED</p>
    <p class="label title-line title-third">SOAK</p>

    <p class="label claim">bath soak to relieve symptoms<br>of mid eczema &amp; itchy, irritated,<br>dry skin</p>
    <p class="label treatment">SOOTHING TREATMENT</p>
    <p class="label net-weight">170g/60oz</p>
    <p class="label product-type">BATH SOAK</p>

    <div class="label brand"><span class="brand-dot"></span><span>TIDEWELL</span></div>
  </main>
</body>
</html>
```